Business cards in digital learning for freelancer

Hello, I need a business cards in french. I work in the Digital learning industries as freeelancer; I'm an expert in digital learning. I work in France. My customer are in the health industry, pharmaceutical industry, and training organization. I've got a logo. I offer three services: consulting, Design, and Training. In the consulting, I offers coaching to choose your digital learning tools and the digital learning strategy. For the Design, I product differents level of elearning like rapid-learning, elearning, micro-learning, video-learning. And for the training service, I've create training about pedagogy, digital learning management project, Digital learning design.
I join my Logo create in this platform. My universe is gamified. I like the life, and I'm very social. I want a card like I'm I. I love Art (painting), Europeen comics. I use in my visual support "permanent maker" font and caracters. I would like cards: elegant, modern, Top class. If you need any information, you can ask me.
thanks for ideas

Target Market(s)

in health industries and training organization for Training manager, instructor, human resources director

Contact Information for Business Card

Phone number : 06 71 38 95 14 , mail: bastiengolmier@quelmoto.fr, web: bastiengolmier.fr , Carrivo

Font styles to use
Sans Serif

Requirements
Must have
• Use my logo and write my 3 services (consulting, training, design)

```html
<!DOCTYPE html>
<html lang="fr">
<head>
<meta charset="utf-8">
<title>Valmorin – cartes de visite</title>
<link rel="stylesheet" href="https://fonts.googleapis.com/css2?family=Arimo:wght@400;700&family=Cinzel:wght@400;600&display=swap">
<style>
  :root {
    --orange: #f07524;
    --orange-soft: #fbe3d3;
    --ink: #5a5a5a;
    --grey-faint: #f1f1f1;
    --white: #ffffff;
    --backdrop: #c9c9c9;
    --social: #1a7bbf;
  }
  * { box-sizing: border-box; margin: 0; padding: 0; }
  html, body { width: 1200px; height: 900px; overflow: hidden; }
  body {
    background: var(--backdrop);
    font-family: "Arimo", Arial, sans-serif;
    position: relative;
  }
  .card {
    position: absolute;
    width: 540px;
    height: 310px;
    border-radius: 26px;
    overflow: hidden;
    box-shadow: 0 6px 18px rgba(0,0,0,0.18);
  }
  /* Back side */
  .card--back {
    left: 60px; top: 90px;
    background: var(--orange);
    color: var(--white);
    display: flex; flex-direction: column;
    align-items: center; justify-content: center;
    gap: 18px;
  }
  .brand-name {
    font-family: "Arimo", Arial, sans-serif;
    font-weight: 700;
    letter-spacing: 3px;
    line-height: 1;
  }
  .card--back .brand-name { font-size: 58px; color: var(--white); }
  .card--back .brand-rule { width: 330px; height: 1px; background: var(--white); opacity: 0.8; }
  .services {
    font-size: 15px; letter-spacing: 1.5px; text-transform: uppercase;
    display: flex; align-items: center; gap: 10px;
  }
  .services .dot { width: 9px; height: 9px; border-radius: 50%; background: var(--white); }

  /* Front side */
  .card--front {
    left: 600px; top: 500px;
    background: var(--white);
    color: var(--ink);
  }
  .front-watermark {
    position: absolute; right: -30px; top: 40px;
    font-weight: 700; font-size: 120px; letter-spacing: 4px;
    color: var(--grey-faint);
    line-height: 1;
    user-select: none;
  }
  .front-brand {
    position: absolute; left: 40px; top: 50px;
  }
  .front-brand .brand-name { font-size: 42px; color: var(--orange); }
  .front-brand .brand-rule { width: 240px; height: 1px; background: var(--ink); margin-top: 10px; }
  .person { position: absolute; left: 40px; top: 150px; }
  .person-name {
    font-family: "Cinzel", "Times New Roman", serif;
    font-weight: 600; font-size: 22px; color: var(--orange);
    letter-spacing: 1px;
  }
  .person-role { font-size: 15px; color: var(--ink); margin-top: 2px; }
  .contact-list { list-style: none; margin-top: 14px; font-size: 14px; }
  .contact-list li { display: flex; align-items: center; gap: 8px; margin-top: 4px; }
  .contact-list svg { width: 15px; height: 15px; flex: none; }
  .social {
    position: absolute; right: 34px; top: 140px;
    display: flex; align-items: center; gap: 6px;
    font-size: 13px; color: var(--social);
  }
  .social .mark { width: 18px; height: 18px; border-radius: 50%; background: var(--social); }
  .website {
    position: absolute; right: 34px; bottom: 78px;
    font-size: 14px; color: var(--ink);
  }
  .website .domain { color: var(--orange); }
</style>
</head>
<body>

  <section class="card card--back" aria-label="Verso de la carte">
    <div class="brand-name">VALMORIN</div>
    <div class="brand-rule"></div>
    <div class="services">
      <span>Consulting</span><span class="dot"></span>
      <span>Training</span><span class="dot"></span>
      <span>Design</span>
    </div>
  </section>

  <section class="card card--front" aria-label="Recto de la carte">
    <div class="front-watermark" aria-hidden="true">VALMORIN</div>

    <div class="front-brand">
      <div class="brand-name">VALMORIN</div>
      <div class="brand-rule"></div>
    </div>

    <div class="person">
      <div class="person-name">Julien Marceau</div>
      <div class="person-role">Managing Director</div>
      <ul class="contact-list">
        <li>
          <svg viewBox="0 0 24 24" aria-hidden="true"><path fill="var(--orange)" d="M6.6 10.8c1.4 2.8 3.8 5.1 6.6 6.6l2.2-2.2c.3-.3.7-.4 1-.2 1.1.4 2.3.6 3.6.6.6 0 1 .4 1 1V20c0 .6-.4 1-1 1C10.6 21 3 13.4 3 4c0-.6.4-1 1-1h3.5c.6 0 1 .4 1 1 0 1.3.2 2.5.6 3.6.1.3 0 .7-.2 1z"/></svg>
          <span>06 71 38 95 14</span>
        </li>
        <li>
          <svg viewBox="0 0 24 24" aria-hidden="true"><rect x="2" y="5" width="20" height="14" rx="1" fill="var(--orange)"/><path d="M2.5 6l9.5 7 9.5-7" stroke="var(--white)" stroke-width="1.6" fill="none"/></svg>
          <span>bastiengolmier@quelmoto.fr</span>
        </li>
      </ul>
    </div>

    <div class="social"><span class="mark"></span><span>Carrivo</span></div>
    <div class="website">www.<span class="domain">bastiengolmier.fr</span></div>
  </section>

</body>
</html>
```